Local Flower Farm Needs Business Card Design

I need business cards designed for a flower farm based in Eudora, Kansas.
Business Info:
We are a local cut flower farm located in Eudora, Kansas, founded by Corinne Haldwick. What started as a passion for agriculture and search for more joy in daily life has blossomed into a small business dedicated to providing the community with beautiful, fresh, and sustainable flowers. We specialize in local, seasonal blooms, ensuring that every petal reflects the care and dedication we pour into our craft. Our mission is to deliver the highest quality flowers directly to our customers through local farmers markets and to florists who share our commitment to sustainability. Join us in celebrating the beauty of nature, one bloom at a time!
Contact Details:
Corinne Haldwick
Owner
Phone 913-555-0147
Facebook: Rosalind Thorpe Gardens
Instagram: @RosalindThorpeGardens
Website: RosalindThorpeGardens.example
Target Market(s)
Wholesale to Florists and Direct to Consumer via Farmers Market
Industry/Entity Type
Florist, Farm
Contact Information for Business Card
Name, Contact Info, Logo
Look and feel
Each slider illustrates characteristics of the customer's brand and the style your logo design should communicate.

```html
<!DOCTYPE html>
<html lang="en">
<head>
<meta charset="utf-8">
<title>Rosalind Thorpe Gardens — Business Cards</title>
<link rel="stylesheet" href="https://fonts.googleapis.com/css2?family=Tinos:wght@400;700&display=swap">
<style>
  :root {
    --stage: #1b1d1e;
    --teal-deep: #061a1d;
    --teal: #0c2a2f;
    --teal-light: #2c5b60;
    --ink: #0a2226;
    --paper: #ffffff;
    --text-font: "Tinos", "Times New Roman", serif;
  }
  * { box-sizing: border-box; margin: 0; padding: 0; }
  html, body { width: 1200px; height: 840px; overflow: hidden; }
  body { background: var(--stage); font-family: var(--text-font); position: relative; }

  .card {
    position: absolute;
    width: 540px;
    height: 310px;
    border-radius: 22px;
    overflow: hidden;
    background: linear-gradient(135deg, var(--teal) 0%, var(--teal-deep) 100%);
    box-shadow: 0 18px 40px rgba(0,0,0,.55);
  }
  .card--front { left: 90px; top: 95px; }
  .card--back { left: 570px; top: 440px; }

  /* Front */
  .brand-seal {
    position: absolute;
    left: 55px; top: 40px;
    width: 230px; height: 230px;
    border: 1.5px solid var(--paper);
    border-radius: 50%;
    display: flex; flex-direction: column;
    align-items: center; justify-content: center;
    color: var(--paper);
    text-align: center;
    letter-spacing: 3px;
    font-size: 19px;
    line-height: 1.35;
  }
  .brand-seal--dark { border-color: var(--ink); color: var(--ink); }
  .brand-accent {
    position: absolute;
    right: 0; top: 0;
    width: 250px; height: 100%;
    background: radial-gradient(ellipse at 65% 55%, rgba(60,120,126,.55) 0%, rgba(20,60,66,.35) 45%, rgba(6,26,29,0) 75%);
  }

  /* Back */
  .back-art { position: absolute; inset: 0; }
  .back-seal {
    position: absolute;
    left: 355px; top: 30px;
    width: 150px; height: 150px;
    font-size: 14px;
    letter-spacing: 2.5px;
  }
  .owner {
    position: absolute;
    left: 40px; top: 128px;
    color: var(--paper);
    max-width: 225px;
  }
  .owner__name { font-weight: 700; font-size: 19px; letter-spacing: .3px; text-transform: uppercase; white-space: nowrap; }
  .owner__role { font-size: 14px; margin-top: 2px; }

  .contact-list {
    position: absolute;
    left: 40px; top: 198px;
    list-style: none;
    color: var(--paper);
    font-size: 15px;
    line-height: 23px;
  }
  .contact-list li { display: flex; align-items: center; gap: 8px; white-space: nowrap; }
  .contact-icon { width: 14px; height: 14px; flex: none; }
  .contact-dot { width: 12px; height: 12px; border-radius: 50%; background: var(--paper); flex: none; margin: 0 1px; }
</style>
</head>
<body>

  <section class="card card--front" aria-label="Business card front">
    <div class="brand-accent" role="img" aria-label="Soft embossed brand decoration"></div>
    <div class="brand-seal">
      <span>ROSALIND</span>
      <span>THORPE</span>
      <span>GARDENS</span>
    </div>
  </section>

  <section class="card card--back" aria-label="Business card back">
    <svg class="back-art" width="540" height="310" viewBox="0 0 540 310" aria-hidden="true">
      <circle cx="430" cy="105" r="148" fill="#ffffff"/>
      <path d="M 283 37 A 162 162 0 0 0 349 245" fill="none" stroke="#ffffff" stroke-width="2"/>
      <circle cx="283" cy="37" r="3.5" fill="#ffffff"/>
      <circle cx="349" cy="245" r="3.5" fill="#ffffff"/>
    </svg>

    <div class="brand-seal brand-seal--dark back-seal">
      <span>ROSALIND</span>
      <span>THORPE</span>
      <span>GARDENS</span>
    </div>

    <div class="owner">
      <p class="owner__name">Corinne Haldwick</p>
      <p class="owner__role">Owner</p>
    </div>

    <ul class="contact-list">
      <li>
        <svg class="contact-icon" viewBox="0 0 24 24" aria-hidden="true"><path fill="#ffffff" d="M6.6 10.8a15.1 15.1 0 0 0 6.6 6.6l2.2-2.2c.3-.3.7-.4 1-.2 1.1.4 2.3.6 3.6.6.6 0 1 .4 1 1V20c0 .6-.4 1-1 1A17 17 0 0 1 3 4c0-.6.4-1 1-1h3.5c.6 0 1 .4 1 1 0 1.3.2 2.5.6 3.6.1.3 0 .7-.2 1z"/></svg>
        913-555-0147
      </li>
      <li><span class="contact-dot"></span>Rosalind Thorpe Gardens</li>
      <li><span class="contact-dot"></span>@RosalindThorpeGardens</li>
      <li>
        <svg class="contact-icon" viewBox="0 0 24 24" aria-hidden="true"><circle cx="12" cy="12" r="10" fill="none" stroke="#ffffff" stroke-width="2"/><path d="M2 12h20M12 2c3 3 3 17 0 20M12 2c-3 3-3 17 0 20" fill="none" stroke="#ffffff" stroke-width="1.6"/></svg>
        RosalindThorpeGardens.example
      </li>
    </ul>
  </section>

</body>
</html>
```